Morvane Capital, a private equity fund, needs a brochure

Morvane Capital is a private equity fund dedicated to the development of budget hotels in France (reasonably priced hotel rooms).
Our customers are French private and high-income investors.

The brochure should communicate :
- seriousness and expertise
- trust, confidence and security
- financial product and profitability

The title is : Investissez dans l'hôtellerie économique et l'immobilier

Brochure size :
3 pages A4
Open size : 63 x 29,7 cm
Closed size : 21 x 29,7 cm

Our competitors :
Trelisse http://trelisse-immo-horizon.example/
789 Parcours http://www.789parcours.example/
GLD Capital http://www.gldam.example/
Soltane capital http://www.soltanecapital.example/
Barostel http://www.barostel.example/

Target Market(s)

Private investors, high-income ; Institutional investors ; Target customers are French private investors with high revenue.

Industry/Entity Type

Financial

Requirements
Must have
• - Brochure must respect our identity (you can see our logo) and use its colors and typo (and/or same typo style)
- You must use pictures on each interior pages (pictures of projetc and hotels)

```html
<!DOCTYPE html>
<html lang="fr">
<head>
<meta charset="utf-8">
<title>Morvane Capital — Hôtellerie et immobilier</title>
<link href="https://fonts.googleapis.com/css2?family=Arimo:wght@400;700&family=PT+Sans+Narrow:wght@700&family=Tinos:wght@400;700&display=swap" rel="stylesheet">
<style>
  :root{
    --backdrop:#2f3436;
    --page:#cbd1d4;
    --ink:#2b2b2b;
    --ink-strong:#1a1a1a;
    --accent:#c0262d;
    --side-top:#a8232b;
    --side-bottom:#8b1a20;
    --visual-warm:#c9a23e;
    --visual-soft:#d9d2b8;
  }
  *{box-sizing:border-box;margin:0;padding:0}
  html,body{width:900px;height:1200px;overflow:hidden}
  body{background:var(--backdrop);position:relative;font-family:"Arimo",Arial,sans-serif;color:var(--ink)}
  .page{position:absolute;left:62px;top:48px;width:776px;height:1107px;background:var(--page)}
  .main{position:absolute;left:33px;top:75px;width:481px;font-size:12.4px;line-height:16.1px;letter-spacing:-0.1px;hyphens:auto;-webkit-hyphens:auto}
  .main p{text-align:justify;margin-bottom:16px}
  .section-title{font-family:"PT Sans Narrow","Arial Narrow",sans-serif;font-weight:700;color:var(--accent);font-size:15px;line-height:16.5px;margin:2px 0 13px;letter-spacing:0}
  .points{list-style:none;margin-bottom:16px;font-weight:700;color:var(--ink-strong)}
  .points li::before{content:"";display:inline-block;width:8px;height:8px;background:var(--accent);margin-right:7px;vertical-align:0}
  .points .cont::before{display:none}
  .sidebar{position:absolute;left:543px;top:0;width:233px;min-height:645px;background:linear-gradient(180deg,var(--side-top),var(--side-bottom));color:#fff;padding:80px 14px 14px 15px}
  .sidebar h2{font-family:"Tinos","Times New Roman",serif;font-weight:700;font-size:16px;line-height:16.5px;margin-bottom:17px}
  .sidebar p{font-family:"Tinos","Times New Roman",serif;font-size:13px;line-height:15.8px;margin-bottom:17px;padding-right:28px}
  .sidebar .facts{list-style:none;font-weight:700;font-size:12px;line-height:15.8px;text-align:justify;hyphens:auto;-webkit-hyphens:auto}
  .sidebar .facts li{margin-bottom:16px}
  .sidebar .facts li:last-child{margin-bottom:0}
  .sidebar .facts li::before{content:"";display:inline-block;width:7px;height:7px;background:#fff;margin-right:6px;vertical-align:1px}
  .key-visual{position:absolute;left:560px;top:672px;width:200px;height:390px;background:radial-gradient(ellipse at 50% 50%,var(--visual-warm) 0%,var(--visual-soft) 55%,var(--page) 85%)}
</style>
</head>
<body>
<div class="page">
  <div class="main">
    <p>L’activité de Morvane Capital est notamment centrée sur l’investissement dans des sociétés développant une activité commerciale d’exploitation d’hôtels économiques. Ces sociétés du portefeuille seront à terme propriétaires des actifs immobiliers qu’elles exploitent.</p>
    <p>Morvane Capital pourra également diversifier ses investissements dans les secteurs de la promotion immobilière et de l’immobilier de service (meublés de tourisme et/ou résidences médicalisées).</p>
    <h3 class="section-title">Des investissements centrés sur l’hôtellerie et l’immobilier</h3>
    <p>Morvane Capital a pour objectif d’accueillir jusqu’à 30 millions d’euro de souscriptions sur 2 ans. Le produit de ces souscriptions permettra la prise de participations minoritaires (40% maximum) dans le capital de sociétés ayant pour objet.</p>
    <ul class="points">
      <li>La construction ou l’acquisition d’hôtels économiques et leur exploitation.</li>
      <li>La construction ou l’acquisition de meublés de tourisme et leur exploitation.</li>
      <li>La construction-vente d’immeuble en VEFA.</li>
    </ul>
    <p>L’activité de Morvane Capital est notamment centrée sur l’investissement dans des sociétés développant une activité commerciale d’exploitation d’hôtels économiques. Ces sociétés du portefeuille seront à terme propriétaires des actifs immobiliers qu’elles exploitent.</p>
    <p>Morvane Capital pourra également diversifier ses investissements dans les secteurs de la promotion immobilière et de l’immobilier de service (meublés de tourisme et/ou résidences médicalisées).</p>
    <h3 class="section-title">Un partenariat avec ARDENNE HOTELS GROUP</h3>
    <p>Pour l’exploitation des investissements hôteliers, les sociétés du portefeuille interviendront en partenariat avec un opérateur hôtelier – ARDENNE HOTELS GROUP – dans le cadre d’un accord de franchise (Ardenne Hotels Group, 2ème opérateur d’Europe, plus de 1000 hôtels dans le monde).</p>
    <ul class="points">
      <li>Contrats de franchise sous enseignes :</li>
      <li class="cont">Étape Claire **, Clocheton *** et Lilas Inn ***.</li>
      <li>Contrats d’assistante technique.</li>
      <li>Implantation de plus de 12 hôtels dans 6 régions françaises d’outremer.</li>
    </ul>
    <h3 class="section-title">Focus sur l’hôtellerie économique<br>dans les régions françaises ultramarines</h3>
    <p>Le marché des hôtels économiques normés et standardisés sous enseigne nationale ou internationale est peu développé dans les DOM-COM. Ces régions sont équipées principalement d’hôtels balnéaires à vocation touristique essentiellement implantés sur des lieux généralement éloignés des centres économiques. Depuis une vingtaine d’années, le développement important des populations et la centralisation des zones commerciales et industrielles sur les capitales administratives ont généré d’importants embouteillages qui compliquent les accès à ces zones. L’offre hôtelière n’est plus en adéquation avec les attentes des visiteurs professionnels. La création d’une chaine d’hôtels économiques est la réponse à ce besoin et bénéficie de l’appui de la puissance publique et des instances régionales.</p>
    <ul class="points">
      <li>Absence d’hôtels économiques standardisés et normés dans ces régions.</li>
      <li>Structures hôtelières existantes inadaptées aux besoins du marché professionnel et coûteuses : prix des nuitées proposées par ces nouveaux hôtels inférieurs de 30 à 50% aux prix pratiqués localement.</li>
      <li>Programmes d’investissements bénéficiant d’avantages fiscaux, sociaux et de subventions.</li>
    </ul>
  </div>

  <aside class="sidebar">
    <h2>Pourquoi l’hôtellerie<br>et l’immobilier?</h2>
    <p>Dans des conditions économiques et financières perturbées depuis la crise financière de 2008, les investisseurs exigent aujourd’hui des placements structurés pour résister aux effets économiques induits. Selon l’analyse des équipes de Morvane Capital, le marché de l’hôtellerie économique en croissance depuis sa création répond particulièrement bien à ces attentes. Ce positionnement est en adéquation avec la baisse des budgets alloués aux déplacements et voyages professionnels et touristiques.</p>
    <ul class="facts">
      <li>Le marché de l’immobilier reste quant à lui une valeur refuge en temps de crise, selon l’analyse des équipes de Morvane Capital.</li>
      <li>Un marché en croissance malgré la crise.</li>
      <li>Sur 2011, la croissance cumulée du nombre de nuitées atteint + 3,2% par rapport à 2010. (source KPRX)</li>
    </ul>
  </aside>

  <div class="key-visual" role="img" aria-label="Photo d’un porte-clés d’hôtel doré avec deux clés suspendues à un anneau"></div>
</div>
</body>
</html>
```